Stationary design for boutique production house

We need a stationary design for our production house, 'Lorno Productions' based in Singapore. We produce microfilms as well as podcasts, talkshows and events. Our logo is a stylized icon of our director, who is also the executive producer and host of our programs, Lorno. Our main company colors are Red, Black and white. We would like a clean, minimalist design incorporating our existing company logo that conveys a sense of urbanism and elegance.

Logo and font files are attached. f

Target Market(s)

We focus on lifestyle media rather than entertainment.

Industry/Entity Type

Boutique

Font styles to use
Serif
Sans Serif

Colors
ec1f27
ffffff
000000

Requirements
Must have
• Our company logo and at least one of our company colors.
Nice to have
• Our address and contact information.
Should not have
• Changes made to the company logo (using only certain parts of it is fine though)

```html
<!DOCTYPE html>
<html lang="en">
<head>
<meta charset="utf-8">
<title>Lorno Productions — Stationery</title>
<link rel="stylesheet" href="https://fonts.googleapis.com/css2?family=Libre+Baskerville&family=Arimo:wght@400&display=swap">
<style>
  :root{
    --red:#ec1f27;
    --deep-red:#b3121a;
    --black:#000000;
    --ink:#1c1c1c;
    --paper:#f4f4f4;
    --white:#ffffff;
    --backdrop:#e8e2d2;
    --serif:"Libre Baskerville", Georgia, serif;
    --sans:"Arimo", Arial, sans-serif;
  }
  *{box-sizing:border-box;margin:0;padding:0}
  html,body{width:1200px;height:1118px;overflow:hidden}
  body{background:var(--backdrop);position:relative;font-family:var(--serif);color:var(--ink)}

  .sheet{position:absolute;background:var(--paper);box-shadow:0 2px 6px rgba(0,0,0,.12);overflow:hidden}

  /* wordmark stand-in */
  .wordmark{display:flex;align-items:center;gap:8px;font-family:var(--serif);color:var(--black);font-weight:400;white-space:nowrap}
  .wordmark .dot{width:10px;height:10px;border-radius:50%;background:var(--red);flex:none}

  /* letterhead */
  .letterhead{left:560px;top:110px;width:560px;height:792px}
  .letterhead__header{height:112px;background:var(--ink);border-bottom:4px solid var(--red);position:relative}
  .letterhead__address{position:absolute;left:350px;top:30px;color:var(--white);font-size:11.5px;line-height:1.45;font-style:normal}
  .letterhead__address .phone{font-family:var(--sans);font-size:10.5px;margin-top:4px}
  .letterhead .wordmark{position:absolute;left:34px;top:44px;color:var(--white);font-size:16px}

  /* envelope */
  .envelope{left:60px;top:170px;width:460px;height:250px}
  .envelope__flap{position:absolute;left:0;top:46px;width:100%;height:4px;background:var(--deep-red)}
  .envelope .wordmark{position:absolute;left:44px;top:130px;font-size:19px}
  .envelope__band{position:absolute;left:0;bottom:0;width:100%;height:46px;background:var(--black);border-top:4px solid var(--red);color:var(--white);font-size:12.5px;display:flex;align-items:center;padding-left:36px}

  /* business cards */
  .card{width:310px;height:176px}
  .card--back{left:70px;top:470px}
  .card--front{left:70px;top:680px}
  .card--back .wordmark{position:absolute;left:14px;top:70px;font-size:10.5px;gap:6px}
  .card--back .wordmark .dot{width:8px;height:8px}
  .card__divider{position:absolute;left:152px;top:18px;width:1px;height:118px;background:var(--red)}
  .card__contacts{position:absolute;left:163px;top:58px;font-size:8.5px;line-height:1}
  .card__contacts li{list-style:none;display:flex;align-items:center;gap:7px;margin-bottom:12px;white-space:nowrap}
  .card__contacts .phone{font-family:var(--sans)}
  .card__contacts svg{width:10px;height:10px;flex:none}
  .card__band{position:absolute;left:0;bottom:0;width:100%;height:22px;background:var(--black);border-top:2px solid var(--red);color:var(--white);font-size:7.5px;display:flex;align-items:center;padding-left:12px;white-space:nowrap}
  .card--front .wordmark{position:absolute;left:0;right:0;top:66px;justify-content:center;font-size:16px}
  .card__band--red{position:absolute;left:0;bottom:0;width:100%;height:26px;background:var(--red);border-top:2px solid var(--black)}
</style>
</head>
<body>

<section class="sheet letterhead" aria-label="Letterhead">
  <div class="letterhead__header">
    <div class="wordmark"><span class="dot"></span>Lorno Productions</div>
    <address class="letterhead__address">
      18 Kallang Way,<br>Harbourlight House,<br>#07 02, Singapore 349250
      <div class="phone">+65 6417 2208</div>
    </address>
  </div>
</section>

<section class="sheet envelope" aria-label="Envelope">
  <div class="envelope__flap"></div>
  <div class="wordmark"><span class="dot"></span>Lorno Productions</div>
  <div class="envelope__band">18 Kallang Way, Harbourlight House, #07 02, Singapore 349250</div>
</section>

<section class="sheet card card--back" aria-label="Business card, contact side">
  <div class="wordmark"><span class="dot"></span>Lorno Productions</div>
  <div class="card__divider"></div>
  <ul class="card__contacts">
    <li class="phone">
      <svg viewBox="0 0 10 10" aria-hidden="true"><rect width="10" height="10" rx="1.5" fill="var(--red)"/><path d="M3 2.5h1.2l.5 1.6-.8.5a4 4 0 0 0 1.5 1.5l.5-.8 1.6.5V7a.6.6 0 0 1-.6.6A4.6 4.6 0 0 1 2.4 3.1.6.6 0 0 1 3 2.5z" fill="#fff"/></svg>
      +65 6417 2208
    </li>
    <li>
      <svg viewBox="0 0 10 10" aria-hidden="true"><rect width="10" height="10" rx="1.5" fill="var(--red)"/><rect x="2" y="3" width="6" height="4" fill="none" stroke="#fff" stroke-width=".8"/><path d="M2 3l3 2.2L8 3" fill="none" stroke="#fff" stroke-width=".8"/></svg>
      hello@lornoproductions.sg
    </li>
  </ul>
  <div class="card__band">18 Kallang Way, Harbourlight House, #07 02, Singapore 349250</div>
</section>

<section class="sheet card card--front" aria-label="Business card, name side">
  <div class="wordmark"><span class="dot"></span>Lorno Productions</div>
  <div class="card__band--red"></div>
</section>

</body>
</html>
```